Company Business Card (Company Promotions)

We want a Business Card that is both Elegant & High Class. We want the card stock thick and unique. We want it to build our Brand Name. We service Automobile dealerships & owners who drive luxury & exotic automobiles that cost an average of $75K. We provide towing services for Luxury & Exotic vehicles. Our colors are Black & Construction Yellow (Gold).
We are manufacture certified for Valdora Kent, RQT, PUKA, ELVO, Tavrine, HJ, Colvesi, Pendrel, Casteduvro, Ombra & Sorvanel. We have authorization to use their logo's.
Enclosed is our old business card. We only used the unusual & Unique brands on the cards but are open to the use of all of them. We also use the Federal Competence Badge that identifies our abilities.

Also enclosed is the name font that we use.

Target Market(s)

Business, Executive, Hi end people that drive finer luxury &/or exotic automobiles.

Industry/Entity Type

Business

Contact Information for Business Card

We market our name. Haul Crestmark. Business address is: 4812 Willowmere Lane, NE Ste: 210, Atlanta, GA 30399 Phone: 404-555-0148. Web address is crestmarkhaul-example.com
Manufacture Certified / Nationally Certified

Font styles to use
Other font styles liked:
• AR DESTINE (in Italic's)

Colors
ffc214

Requirements
Must have
• Must have the at least 5 of the manufacture logo's and the Guild Council Emblem (see on other business card)
Nice to have
• Place the manfacture logo's on the back.
Should not have
• No other colors than Black, Yellow & White

```html
<!DOCTYPE html>
<html lang="en">
<head>
<meta charset="utf-8">
<title>Haul Crestmark – Business Card</title>
<link href="https://fonts.googleapis.com/css2?family=Orbitron:wght@700;900&family=Arimo:wght@400;700&display=swap" rel="stylesheet">
<style>
  :root {
    --black: #0b0b0b;
    --black-soft: #1c1c1c;
    --plate-dark: #141414;
    --plate-light: #2e2e2e;
    --yellow: #ffc214;
    --white: #ffffff;
    --page: #e9e9e9;
  }
  * { box-sizing: border-box; margin: 0; padding: 0; }
  html, body { width: 1200px; height: 892px; overflow: hidden; }
  body {
    background: var(--page);
    display: flex;
    align-items: center;
    justify-content: center;
    gap: 40px;
    font-family: "Arimo", Arial, sans-serif;
  }
  .card {
    position: relative;
    width: 560px;
    height: 320px;
    background: var(--black);
    overflow: hidden;
    box-shadow: 0 6px 18px rgba(0,0,0,.25);
  }
  .card__shine {
    position: absolute; inset: 0;
    background: linear-gradient(115deg, rgba(255,255,255,.08) 0%, rgba(255,255,255,0) 45%, rgba(255,255,255,.05) 70%, rgba(255,255,255,0) 100%);
  }
  .plate {
    position: absolute; left: 0; right: 0;
    background: linear-gradient(180deg, var(--plate-dark), var(--plate-light) 55%, var(--plate-dark));
  }
  .card--front .plate { top: 70px; height: 180px; }
  .card--back .plate { bottom: 0; height: 80px; }

  .brand {
    position: absolute;
    left: 36px; right: 36px;
    font-family: "Orbitron", sans-serif;
    font-style: italic;
    color: var(--yellow);
  }
  .card--front .brand { top: 26px; }
  .card--back .brand { top: 92px; }
  .brand__first { display: block; font-size: 30px; font-weight: 900; line-height: 1; }
  .brand__main {
    display: block; text-align: right;
    font-size: 46px; font-weight: 900; line-height: 1;
    margin-top: -4px;
  }
  .brand__rule { height: 3px; background: var(--yellow); margin: 6px 0 6px; }
  .brand__tagline {
    display: block;
    font-family: "Orbitron", sans-serif;
    font-weight: 700;
    font-size: 13px;
    color: var(--white);
    letter-spacing: .5px;
  }

  .contact {
    position: absolute;
    left: 36px; right: 36px; top: 170px;
    color: var(--yellow);
    text-align: center;
  }
  .contact__phone { font-size: 22px; }
  .contact__web { font-size: 22px; }
  .contact__address { font-size: 13.5px; margin-top: 4px; }

  .makers {
    position: absolute;
    left: 0; right: 0; bottom: 0; height: 58px;
    background: var(--white);
    display: flex;
    align-items: center;
    justify-content: space-around;
    padding: 0 8px;
  }
  .makers__name {
    font-family: "Arimo", sans-serif;
    font-weight: 700;
    font-size: 9px;
    color: var(--black);
    text-align: center;
    max-width: 58px;
  }
  .emblem {
    width: 26px; height: 26px;
    background: var(--black);
    border-radius: 50%;
    flex: none;
  }
</style>
</head>
<body>

  <section class="card card--front" aria-label="Card front">
    <div class="plate" role="img" aria-label="Diamond steel plate texture"></div>
    <div class="card__shine"></div>
    <h1 class="brand">
      <span class="brand__first">Haul</span>
      <span class="brand__main">CRESTMARK</span>
      <div class="brand__rule"></div>
      <span class="brand__tagline">Manufacture Certified / Nationally Certified</span>
    </h1>
    <div class="contact">
      <p class="contact__phone">404-555-0148</p>
      <p class="contact__web">www.crestmarkhaul-example.com</p>
      <p class="contact__address">4812 Willowmere Lane, NE Ste: 210, Atlanta, GA 30399</p>
    </div>
    <ul class="makers" style="list-style:none">
      <li class="makers__name">Valdora Kent</li>
      <li class="makers__name">Brenhollow</li>
      <li class="makers__name">Ironmarsh</li>
      <li class="makers__name">Trivanto</li>
      <li class="makers__name">Tavrine</li>
      <li class="makers__name">Lynxhall</li>
      <li class="emblem" role="img" aria-label="Guild Council Emblem"></li>
      <li class="makers__name">ELVO</li>
      <li class="makers__name">RQT</li>
    </ul>
  </section>

  <section class="card card--back" aria-label="Card back">
    <div class="plate" role="img" aria-label="Diamond steel plate texture"></div>
    <div class="card__shine"></div>
    <h2 class="brand">
      <span class="brand__first">Haul</span>
      <span class="brand__main">CRESTMARK</span>
      <div class="brand__rule"></div>
      <span class="brand__tagline">Manufacture Certified / Nationally Certified</span>
    </h2>
  </section>

</body>
</html>
```